World Wide News and Current Affairs website

We intends to start up a new website which deals on New and Current Affairs.
Attention Designers,
We want a home page design for this project. Our business is based in the United States. Our goal is to become a well known brand.
The website would consist of a category for News, Business and Tech.
The theme should be beautiful and attention seeking. The website would take bulk of it's news from the US, and Europe.
Designers can get inspiration from already existing new websites such as PWJ, KLV, DASKOLM.
All designs should be clean and easy to navigate.

```html
<!DOCTYPE html>
<html lang="en">
<head>
<meta charset="utf-8">
<title>Worldwide News Home</title>
<link href="https://fonts.googleapis.com/css2?family=Roboto+Condensed:wght@400;700&family=Roboto:wght@400;500;700&display=swap" rel="stylesheet">
<style>
:root{
  --bg:#f1f2f4;--panel:#fff;--side:#243140;--side-text:#b9c3cf;
  --blue:#1e9bd7;--red:#e8412a;--ink:#1f2328;--muted:#8a9099;--line:#e6e8eb;
}
*{box-sizing:border-box;margin:0;padding:0}
html,body{width:790px;height:1200px;overflow:hidden}
body{background:var(--bg);font-family:Roboto,sans-serif;color:var(--ink);position:relative;font-size:5px}
.sidebar{position:absolute;left:0;top:0;width:66px;height:1174px;background:var(--side)}
.brand{color:#fff;font:700 17px 'Roboto Condensed',sans-serif;padding:6px 9px}
.side-nav{list-style:none;margin-top:28px}
.side-nav li{display:flex;align-items:center;gap:6px;padding:0 9px;height:16.5px;color:var(--side-text);font:500 4.6px Roboto,sans-serif;letter-spacing:.2px;white-space:nowrap}
.side-nav li.on{color:#fff}
.side-nav i{width:5px;height:5px;border-radius:1px;background:currentColor;display:block;flex:none}
.topbar{position:absolute;left:74px;top:8px;width:708px;height:25px;background:var(--panel);display:flex;align-items:center;padding:0 8px;font:500 4.6px Roboto,sans-serif}
.topbar a{margin-right:16px;color:var(--ink);text-decoration:none}
.topbar a.on{color:var(--red)}
.tools{margin-left:auto;display:flex;gap:22px}
.tools span{width:5px;height:5px;border:1.2px solid var(--ink);border-radius:50%}
.panel{position:absolute;background:var(--panel)}
.ptitle{font:700 7px 'Roboto Condensed',sans-serif;display:flex;align-items:center;gap:5px}
.ptitle:after{content:"";width:8px;height:1px;background:var(--blue)}
.ph{position:absolute;overflow:hidden}
.cap{position:absolute;left:0;right:0;bottom:6px;text-align:center;color:#fff;font:700 5.6px 'Roboto Condensed',sans-serif;line-height:1.35;padding:0 6px}
.tag{position:absolute;left:0;top:8px;background:var(--red);color:#fff;font:4px Roboto,sans-serif;padding:3px 6px}
.latest{left:74px;top:272px;width:588px;height:820px}
.item{position:absolute;left:8px;right:8px;height:100.5px;border-bottom:1px solid var(--line)}
.item .ph{left:0;top:8px;width:124px;height:85px}
.item .txt{position:absolute;left:136px;right:6px;top:10px}
.meta{font:4px Roboto,sans-serif;color:var(--muted)}
.ttl{font:700 6px 'Roboto Condensed',sans-serif;margin:9px 0 8px}
.ttl.red{color:var(--red)}
.body{font:4.3px/1.85 Roboto,sans-serif;color:#555}
.right{left:670px;width:112px}
.rhead{font:700 6.6px 'Roboto Condensed',sans-serif;padding:6px 8px;border-top:2px solid var(--blue)}
.small{font:3.6px Roboto,sans-serif;color:var(--muted)}
.btn{background:var(--blue);color:#fff;font:500 4.4px Roboto,sans-serif;text-align:center}
.cal{display:grid;grid-template-columns:repeat(7,1fr);gap:2px 1px;font:4px Roboto,sans-serif;text-align:center}
.cal b{font-weight:400;font-size:3.2px;color:var(--muted);background:#f1f2f4;padding:1px 0}
.cal span{padding:2px 0}
.cal .mut{color:#aaa}
.cal .today{background:var(--blue);color:#fff}
.pop{display:flex;gap:5px;margin-bottom:7.5px}
.pop .ph{position:static;width:34px;height:24px;flex:none}
.pop p{font:700 4.2px/1.3 'Roboto Condensed',sans-serif}
.day{text-align:center;width:24px}
.day svg{display:block;margin:3px auto}
.foot{position:absolute;left:256px;top:1138px;display:flex;gap:14px;font:500 4.5px Roboto,sans-serif}
.bottom{position:absolute;left:0;top:1174px;width:790px;height:26px;background:#fff;border-top:1px solid var(--line)}
</style>
</head>
<body>
<aside class="sidebar">
  <div class="brand">LOGO</div>
  <ul class="side-nav">
    <li class="on"><i></i>HOME</li><li><i></i>REGIONS</li><li><i></i>WORLD</li><li><i></i>ELECTIONS</li>
    <li><i></i>BUSINESS</li><li><i></i>TECH</li><li><i></i>SPORTS</li><li><i></i>ENTERTAINMENT</li><li><i></i>HEALTH</li>
  </ul>
</aside>

<nav class="topbar">
  <a class="on">TOP STORIES</a><a>NORTH AMERICA</a><a>SOUTH AMERICA</a><a>AFRICA</a><a>EUROPE</a><a>ASIA PACIFIC</a><a>AUSTRALIA</a><a>ANTARCTICA</a>
  <div class="tools"><span></span><span></span><span></span></div>
</nav>

<section class="panel" style="left:74px;top:42px;width:588px;height:222px">
  <div class="ptitle" style="position:absolute;left:8px;top:6px">TRENDING POST</div>
  <div class="ph" style="left:8px;top:20px;width:282px;height:194px;background:linear-gradient(#e88a3a,#f5c27a 45%,#8a7a78 75%,#c9b9b0)" role="img" aria-label="Red suspension bridge above fog at sunset">
    <span class="tag">Architects</span>
    <div class="cap" style="bottom:12px">Spectacular New Bridges That Break The Mold<br><span style="font:400 4.4px Roboto,sans-serif;display:block;margin-top:8px">In a world of bamboo skyscrapers and transforming apartments, it's easy to forget about the bridge,<br>the humble structure that makes getting from point A to B all the more simple.</span></div>
  </div>
  <div class="ph" style="left:298px;top:20px;width:137px;height:93px;background:linear-gradient(#5b87b8,#9fbbd6 55%,#6c7a72)" role="img" aria-label="Passenger jet on a runway"><div class="cap">Aerolux Flight Crashes With<br>66 People On Board</div></div>
  <div class="ph" style="left:443px;top:20px;width:137px;height:93px;background:linear-gradient(120deg,#d8cfc2,#b59a86 60%,#6e5a4c)" role="img" aria-label="Woman relaxing on a sofa"><div class="cap">'Eat Well, Skip That': Essential<br>Food Guide for Moms-to-Be</div></div>
  <div class="ph" style="left:298px;top:121px;width:137px;height:93px;background:linear-gradient(#78a9d0,#c9b9a0 55%,#8aa4a8)" role="img" aria-label="Woman sunbathing on a rocky coast"><div class="cap">Sexy, Gender And Morality: The<br>Unseen History Of Underwear</div></div>
  <div class="ph" style="left:443px;top:121px;width:137px;height:93px;background:linear-gradient(#9fb6c9,#566572 70%,#3a4148)" role="img" aria-label="Modern glass apartment building"><div class="cap">Navy Will Use 3-D Printed Part<br>In Kestrel Aircraft</div></div>
</section>

<section class="panel latest">
  <div class="ptitle" style="position:absolute;left:8px;top:4px">LATEST POST</div>
  <div style="position:absolute;right:8px;top:6px;display:flex;gap:3px"><span style="width:5px;height:4px;background:var(--muted)"></span><span style="width:5px;height:4px;background:var(--blue)"></span></div>

  <article class="item" style="top:14px"><div class="ph" style="background:linear-gradient(#2c3a6a,#c9733a 60%,#d8a060)" role="img" aria-label="Basketball game on an indoor court"></div>
    <div class="txt"><p class="meta">Sport News - 18 Minutes ago</p><h3 class="ttl">Back And Now It's The Comets' Turn To Counter</h3><p class="body">As Dale Morrow admitted before the Tides' 118-91 Game 2 victory over the Harbor City Comets on Wednesday to tie the Western Conference Finals at 1-1, there's a "fine line" between good shots and bad shots for the Tides. In losses such as Game 1, the Tides' shot selection tends to trend toward the latter (bad shots). In Game 2, their shot distribution was more of the former (good ones).</p></div></article>

  <article class="item" style="top:114.5px"><div class="ph" style="background:linear-gradient(#6f7f8c,#8f9ca4 55%,#4d5860)" role="img" aria-label="City skyline viewed across a bay"></div>
    <div class="txt"><p class="meta">Architects - 48 Minutes ago</p><h3 class="ttl red">30 Stunning Feats Of Design Battle To Be The World's Best Building</h3><p class="body">Featuring invisible houses and flora-clad towers, a thirty-strong shortlist of architectural projects from around the world has been unveiled today by the Global Institute of Architects (GIA) for its inaugural GIA International Prize. The buildings, which range from a cultural center in Azerbaijan to a kindergarten in Vietnam, have been selected to compete for a prize that the organizers say will go to "the most significant and inspirational building of the year."</p></div></article>

  <article class="item" style="top:215px"><div class="ph" style="background:linear-gradient(90deg,#cfe3ea,#7fb0b8 50%,#e4eef0)" role="img" aria-label="Hospital corridor with staff in scrubs"></div>
    <div class="txt"><p class="meta">Health - 2 Hours ago</p><h3 class="ttl">Major Eastport Hospital To Offer Gender-Reassignment Surgerie</h3><p class="body">A Major Eastport academic hospital said on Wednesday it would become the first in the northeastern United States to begin performing gender-reassignment surgery on transgender patients. Eastport Medical Center, which has been providing transgender patients with hormone therapy and facial and chest surgery since the 1990s, said it would begin performing a male-to-female procedure it calls "gender affirmation" surgery beginning this summer.</p></div></article>

  <article class="item" style="top:315.5px"><div class="ph" style="background:linear-gradient(#8cc3e4,#c7b49a 60%,#5a7c8c)" role="img" aria-label="Woman in white swimsuit at the beach"></div>
    <div class="txt"><p class="meta">Fashion &amp; Lifestyle - 3 Hours ago</p><h3 class="ttl">Builds on Multimedia Platform for Beach Lifestyle</h3><p class="body">It's mental, emotional and spiritual, says Owen Fairley, a clinical hypnotherapist who specializes in helping his patients with relationship issues. "Average sex is where you're experiencing satisfaction in one or two of those four ways, and feel it could be better. Mind-blowing sex is when you're connecting mentally, emotionally, spiritually and physically while nurturing [your] own and [your] partner's desires," he says.</p></div></article>

  <article class="item" style="top:416px"><div class="ph" style="background:linear-gradient(#6fa7dc,#b8cde0 55%,#d9dde0)" role="img" aria-label="Curved modern landmark building"></div>
    <div class="txt"><p class="meta">Architect - 4 Hours ago</p><h3 class="ttl">An Exclusive Look Inside Helsinki's Experimental New Landmark</h3><p class="body">A Major Eastport academic hospital said on Wednesday it would become the first in the northeastern United States to begin performing gender-reassignment surgery on transgender patients. Eastport Medical Center, which has been providing transgender patients with hormone therapy and facial and chest surgery since the 1990s, said it would begin performing a male-to-female procedure it calls "gender affirmation" surgery beginning this summer.</p></div></article>

  <article class="item" style="top:516.5px"><div class="ph" style="background:linear-gradient(90deg,#e9e4de,#c9a890 50%,#b8403a)" role="img" aria-label="Couple embracing at home"></div>
    <div class="txt"><p class="meta">Entertainment - 5 Hours ago</p><h3 class="ttl">5 Steps For Saving a Marriage After an Affair</h3><p class="body">These are the emotions people harbor after finding out their spouse has been cheating on them. Many of us know marriages which broke up because of an affair, but that's not what I'm addressing here. Before you even begin the path towards processing the affair, it's easier to know there will be a light at the end of the tunnel. In my 25-plus years of working as a psychologist. They key is to have every key, the key to open every door. We don't see them, we will never see them.</p></div></article>

  <article class="item" style="top:617px"><div class="ph" style="background:linear-gradient(#9ec5e6,#c4ccd2 45%,#3f8a3c 70%,#8a8a8a)" role="img" aria-label="Vintage green truck on a street"></div>
    <div class="txt"><p class="meta">Transport - 17 Hours ago</p><h3 class="ttl">Whitcombe Sewing Machine Company</h3><p class="body">Whitcombe's brother Hartwell, who was a management talent, joined the business venture, followed by their brother Edwin, who became instrumental in the sales, promotion and distribution of the product. The first group of fifty cars were completed in October 1900, but none were offered to the public until April 1901 so the design could be thoroughly tested. They never said winning was easy. Some people can't handle success</p></div></article>

  <article class="item" style="top:717.5px;border:0"><div class="ph" style="background:linear-gradient(90deg,#f1ece6,#d9b8a0 55%,#c94a3a)" role="img" aria-label="Mother and daughter cooking in a kitchen"></div>
    <div class="txt"><p class="meta">Food &amp; Drink - 22 Hours ago</p><h3 class="ttl">Cook Looks Into The Saucepan In Kitchen</h3><p class="body">These are the emotions people harbor after finding out their spouse has been cheating on them. Many of us know marriages which broke up because of an affair, but that's not what I'm addressing here. Before you even begin the path towards processing the affair, it's easier to know there will be a light at the end of the tunnel. In my 25-plus years of working as a psychologist. They key is to have every key, the key to open every door. We don't see them, we will never see them.</p></div></article>
</section>

<section class="panel right" style="top:42px;height:108px">
  <div class="rhead" style="display:flex;align-items:baseline;gap:3px">LONDON <span class="small">ENGLAND</span></div>
  <svg style="position:absolute;left:10px;top:22px" width="22" height="16" viewBox="0 0 22 16"><circle cx="8" cy="7" r="5" fill="none" stroke="var(--red)" stroke-width="1.4"/><path d="M6 10h12a3 3 0 0 0 0-6 5 5 0 0 0-9-1" fill="#fff" stroke="var(--red)" stroke-width="1.4"/><path d="M9 13l-1 2M13 13l-1 2M17 13l-1 2" stroke="var(--red)" stroke-width="1.2"/></svg>
  <div style="position:absolute;left:8px;top:46px;font:4px Roboto,sans-serif;color:var(--red)">SUMMER RAIN</div>
  <div style="position:absolute;left:57px;top:30px;font:400 13px Roboto,sans-serif">22<sup style="font-size:5px">°</sup></div>
  <div class="small" style="position:absolute;left:57px;top:47px">24km / h / 66%</div>
  <div style="position:absolute;left:8px;right:8px;top:66px;border-top:1px solid var(--line);display:flex;justify-content:space-between;padding-top:4px" class="small">
    <div class="day">FRIDAY<svg width="12" height="9" viewBox="0 0 12 9"><path d="M3 7h6a2 2 0 0 0 0-4 3 3 0 0 0-6 1 1.5 1.5 0 0 0 0 3z" fill="none" stroke="#9aa0a8" stroke-width=".7"/></svg><span style="color:var(--ink)">18 °</span></div>
    <div class="day">SATURDAY<svg width="12" height="9" viewBox="0 0 12 9"><circle cx="6" cy="3" r="1.6" fill="none" stroke="#9aa0a8" stroke-width=".7"/><path d="M3 8h6a2 2 0 0 0 0-3.5H3a1.7 1.7 0 0 0 0 3.5z" fill="#fff" stroke="#9aa0a8" stroke-width=".7"/></svg><span style="color:var(--ink)">28 °</span></div>
    <div class="day">SUNDAY<svg width="12" height="9" viewBox="0 0 12 9"><path d="M3 6h6a2 2 0 0 0 0-4 3 3 0 0 0-6 1 1.5 1.5 0 0 0 0 3zM5 7l-.5 1.5M7 7l-.5 1.5" fill="none" stroke="#9aa0a8" stroke-width=".7"/></svg><span style="color:var(--ink)">32 °</span></div>
  </div>
</section>

<section class="panel right" style="top:157px;height:219px">
  <div class="rhead">THE <span style="color:var(--red)">BIG</span>BOARD</div>
  <div style="padding:0 8px">
    <p style="font:700 4.4px Roboto,sans-serif;margin-top:4px">PBL</p>
    <p class="small" style="display:flex;justify-content:space-between;margin-top:5px"><span>FINAL</span><span>12:25 PM - WED, MAY 18</span></p>
    <div style="display:flex;align-items:center;gap:5px;margin-top:8px;font:4px Roboto,sans-serif"><span style="width:11px;height:9px;background:var(--blue);border-radius:50%"></span><span class="small" style="color:var(--ink)">HARBOR CITY<br>COMETS</span><span style="margin-left:auto;font-size:5px">88</span></div>
    <div style="display:flex;align-items:center;gap:5px;margin-top:6px"><span style="width:10px;height:10px;background:#1e5fa8;border-radius:50%"></span><span class="small" style="color:var(--ink)">BAY STATE<br>TIDES</span><span style="margin-left:auto;font-size:5px">192</span></div>
    <p class="small" style="margin-top:9px"><span style="color:var(--red)">HCC</span> R VANCE 29 PTS &nbsp; <span style="color:var(--red)">BST</span> T HALE 28 PTS</p>
    <div style="border-top:1px solid var(--line);margin-top:6px"></div>
    <p style="font:700 4.4px Roboto,sans-serif;margin-top:6px">FOOTBALL</p>
    <p class="small" style="display:flex;justify-content:space-between;margin-top:5px"><span>FINAL</span><span>11:25 PM - WED, MAY 18</span></p>
    <div style="display:flex;align-items:center;gap:5px;margin-top:9px;font-size:4.6px"><svg width="13" height="9"><rect width="13" height="3" fill="#111"/><rect y="3" width="13" height="3" fill="#d00"/><rect y="6" width="13" height="3" fill="#fc0"/></svg>GER<span style="margin-left:auto">2</span></div>
    <div style="display:flex;align-items:center;gap:5px;margin-top:8px;font-size:4.6px"><svg width="13" height="9"><rect width="4.3" height="9" fill="#0b3fa6"/><rect x="4.3" width="4.4" height="9" fill="#fff"/><rect x="8.7" width="4.3" height="9" fill="#e8262b"/></svg>FRA<span style="margin-left:auto">1</span></div>
    <p class="small" style="margin-top:9px"><span style="color:var(--red)">GER</span> R VANCE 29 MINS &nbsp;<span style="color:var(--red)">FRA</span> T HALE 28 MINS</p>
    <div class="btn" style="margin-top:9px;padding:5px 0">VIEW MORE</div>
  </div>
</section>

<div class="small" style="position:absolute;left:750px;top:386px;font-size:3px">ADVERTISEMENT</div>
<div class="ph" style="left:670px;top:392px;width:112px;height:106px;background:linear-gradient(100deg,#f2a516 45%,#f7d28a 70%,#8cc2e6)" role="img" aria-label="Travel banner with couple on holiday">
  <div style="position:absolute;left:10px;top:31px;color:#fff;font:700 9px 'Roboto Condensed',sans-serif">BANNER</div>
  <div style="position:absolute;left:10px;top:45px;color:#fff;font:4px Roboto,sans-serif">BEST TRAVEL DEALS</div>
  <div style="position:absolute;left:7px;top:60px;color:#fff;font:700 13px 'Roboto Condensed',sans-serif">75% OFF</div>
</div>

<section class="panel right" style="top:507px;height:181px">
  <div style="display:flex;height:16px;font:700 6px 'Roboto Condensed',sans-serif;align-items:center"><span style="background:var(--blue);color:#fff;padding:4px 8px;height:16px">POPULAR</span><span style="padding:0 7px;color:var(--muted);border-top:2px solid var(--blue);height:16px;line-height:14px;flex:1">COMMENTS &nbsp;‹ ›</span></div>
  <div style="padding:8px 8px 0">
    <div class="pop"><div class="ph" style="background:linear-gradient(#8fa3b3,#5a5448)" role="img" aria-label="House on a cliff"></div><p>This Home Is Being Built Into A Cliff<br><span class="small" style="font-weight:400">28 Apr 2016</span></p></div>
    <div class="pop"><div class="ph" style="background:linear-gradient(#f1e6b0,#d6a84a)" role="img" aria-label="Food truck kitchen"></div><p>How To Spice Up A Neutral Kitchen<br><span class="small" style="font-weight:400">24 Apr 2016</span></p></div>
    <div class="pop"><div class="ph" style="background:linear-gradient(90deg,#3a5c9a,#d86a3a)" role="img" aria-label="Crowd at a concert"></div><p>Mara Delaney Discusses the Reunion of Driftwood<br><span class="small" style="font-weight:400">18 Apr 2016</span></p></div>
    <div class="pop"><div class="ph" style="background:linear-gradient(#6d8fb0,#3e4650)" role="img" aria-label="House on a cliff"></div><p>This Home Is Being Built Into A Cliff<br><span class="small" style="font-weight:400">16 Apr 2016</span></p></div>
    <div class="pop"><div class="ph" style="background:linear-gradient(#7895b8,#1c2a44)" role="img" aria-label="Blue car"></div><p>This Home Is Being Built Into A Cliff<br><span class="small" style="font-weight:400">12 Apr 2016</span></p></div>
  </div>
</section>

<div class="ph" style="left:670px;top:696px;width:112px;height:76px;background:linear-gradient(#c9d1d8,#8d99a4 55%,#3f4a55)" role="img" aria-label="Cruise ship at sea">
  <svg style="position:absolute;left:9px;top:9px" width="16" height="16"><circle cx="8" cy="8" r="7" fill="none" stroke="#fff" stroke-width="1"/><path d="M6.5 5v6l5-3z" fill="#fff"/></svg>
  <div class="cap">Navy Will Use 3-D Printed Part<br>In Kestrel Aircraft</div>
</div>

<section class="panel right" style="top:780px;height:92px;border-top:2px solid var(--blue);text-align:center">
  <p style="font:700 6.6px/1.35 'Roboto Condensed',sans-serif;margin-top:7px">SUBSCRIBE TO OUR<br>NEWSLETTER</p>
  <p class="small" style="margin-top:6px;font-size:4px">We Promise Not to Spam</p>
  <div class="small" style="margin:8px 8px 0;border:1px solid var(--line);padding:5px 0">Email Address...</div>
  <div class="btn" style="margin:6px 8px 0;padding:5px 0">✉ &nbsp;SUBSCRIBE</div>
</section>

<div class="ph" style="left:670px;top:880px;width:112px;height:76px;background:linear-gradient(#b9cfe4,#7f8c98 55%,#2e343a)" role="img" aria-label="City street with cars">
  <span style="position:absolute;left:0;top:30px;width:10px;height:12px;background:rgba(0,0,0,.5);color:#fff;font:7px Roboto;text-align:center">‹</span>
  <span style="position:absolute;right:0;top:30px;width:10px;height:12px;background:var(--blue);color:#fff;font:7px Roboto;text-align:center">›</span>
  <div class="cap">Navy Will Use 3-D Printed Part<br>In Kestrel Aircraft</div>
</div>

<section class="panel right" style="top:964px;height:124px">
  <div class="rhead">CALENDAR</div>
  <div style="margin:6px 8px 0;background:#f1f2f4;display:flex;justify-content:space-between;align-items:center;padding:2px 3px;font:700 4.6px Roboto,sans-serif"><span>‹</span>March 2012<span style="width:6px;height:6px;background:var(--blue);border-radius:50%"></span></div>
  <div class="cal" style="margin:3px 8px 0">
    <b>MON</b><b>TUE</b><b>WED</b><b>THU</b><b>FRI</b><b>SAT</b><b>SUN</b>
    <span class="mut">28</span><span>1</span><span>2</span><span>3</span><span class="today">4</span><span>5</span><span>6</span>
    <span>7</span><span>8</span><span>9</span><span>10</span><span>11</span><span>12</span><span>13</span>
    <span>14</span><span>15</span><span>16</span><span>17</span><span>18</span><span>19</span><span>20</span>
    <span>21</span><span>22</span><span>23</span><span>24</span><span>25</span><span>26</span><span>27</span>
    <span>28</span><span>29</span><span>30</span><span>31</span><span class="mut">1</span><span class="mut">2</span><span class="mut">3</span>
  </div>
</section>

<div style="position:absolute;left:296px;top:1108px;width:144px;height:16px;background:#fff;border:1px solid #d9dcdf;text-align:center;font:4.6px/14px Roboto,sans-serif">Show More Results</div>
<nav class="foot"><span>HOME</span><span>BLOG</span><span>ABOUT US</span><span>CONTACT US</span><span>HELP</span><span>PRIVACY</span><span>TERMS OF USE</span></nav>

<footer class="bottom">
  <span style="position:absolute;left:8px;top:7px;width:42px;height:13px;background:#111;border-radius:2px"></span>
  <span style="position:absolute;left:58px;top:7px;width:42px;height:13px;background:#111;border-radius:2px"></span>
  <span class="small" style="position:absolute;left:676px;top:11px;font-size:4px">Privacy Policy</span>
  <span class="small" style="position:absolute;left:710px;top:11px;font-size:4px">Terms of Service</span>
  <span style="position:absolute;left:751px;top:7px;width:31px;height:12px;background:#111;color:#fff;font:500 4.6px/12px Roboto,sans-serif;text-align:center">SHARE</span>
</footer>
</body>
</html>
```